Brisk Harbor claims recovery services

Its a new company in Dubai UAE. The company activity is debt management, debt collection, loans settlements and restructuring. The company involved in any business or sector requires debt management including government entities, Medical & Health care sector, Banks & finance companies, SME's and commercial business.

Target Market(s)

government entities, Medical & Health care sector, Banks & finance companies, SME's and commercial business.

Industry/Entity Type

Financial Service

Number of Pages Required

5+ page

Requirements
Must have
• Focus on the services not the team and clients
Should not have
• Colorful . Shouldn't have Client testimonial and our clients

```html
<!DOCTYPE html>
<html lang="en">
<head>
<meta charset="utf-8">
<title>Brisk Harbor – Our Services</title>
<link rel="stylesheet" href="https://fonts.googleapis.com/css2?family=Cinzel:wght@400;700&family=Open+Sans:ital,wght@0,400;0,600;0,700;1,400&family=Roboto:wght@400;500;700&display=swap">
<style>
:root{
  --navy:#0f5a85;
  --navy-dark:#0c4a72;
  --footer:#0d4a73;
  --ink:#333a40;
  --muted:#7d858c;
  --line:#e4e7ea;
  --band:#f3f4f5;
  --soft:#9aa0a5;
}
*{margin:0;padding:0;box-sizing:border-box}
html,body{width:775px;height:1200px;overflow:hidden;background:#fff}
body{position:relative;font-family:"Open Sans",sans-serif;color:var(--ink)}
.abs{position:absolute}

/* header */
.brand{display:flex;align-items:center;gap:7px}
.brand-mark{width:14px;height:14px;background:var(--navy)}
.brand-name{font-family:"Cinzel",serif;font-size:17px;color:var(--navy);letter-spacing:.5px;white-space:nowrap}
.brand-tag{font-family:"Cinzel",serif;font-size:4.3px;letter-spacing:3px;color:var(--muted);margin-left:21px;margin-top:2px;white-space:nowrap}
.call{left:433px;top:26px;display:flex;align-items:center;gap:6px;font-size:7.5px;color:var(--muted)}
.call-icon{width:24px;height:24px;border:1.5px solid var(--navy);border-radius:50%;display:flex;align-items:center;justify-content:center}
.call strong{color:var(--navy);font-weight:700;font-size:8.5px}
.quote-btn{left:601px;top:24px;width:110px;height:27px;background:var(--navy-dark);color:#fff;font-size:7px;font-weight:600;display:flex;align-items:center;justify-content:center;border-radius:2px}

/* nav */
.main-nav{left:0;top:73px;width:775px;height:34px;background:linear-gradient(#b2b5b8,#97999c)}
.nav-item{position:absolute;top:0;height:34px;line-height:34px;color:#fff;font-size:7px;text-transform:uppercase;transform:translateX(-50%);white-space:nowrap}
.nav-active{left:342px;top:0;width:87px;height:34px;background:var(--navy)}

/* hero */
.hero{left:0;top:107px;width:775px;height:247px;background:radial-gradient(ellipse at 70% 40%,#33465c 0%,#1e2d3f 55%,#121b27 100%)}
.hero-title{left:122px;top:205px;font-family:"Cinzel",serif;font-size:19px;color:#fff;letter-spacing:.5px}
.hero-sub{left:122px;top:238px;font-family:"Cinzel",serif;font-size:12px;color:#fff;letter-spacing:1px}

/* services */
.section-title{left:0;width:775px;top:380px;text-align:center;font-family:"Roboto",sans-serif;font-size:17px;color:var(--navy);font-weight:500}
.section-intro{left:170px;width:435px;top:405px;text-align:center;font-size:8px;line-height:16px;color:var(--muted)}
.service-badge{width:122px;height:122px;border-radius:50%;border:3px solid #eef0f2;overflow:hidden;background:linear-gradient(160deg,#eef1f4,#c9d3dc)}
.service-badge svg{position:absolute;left:50%;top:26px;transform:translateX(-50%)}
.badge-band{position:absolute;left:0;bottom:0;width:100%;height:36%;background:var(--navy);color:#fff;text-align:center;padding-top:8px}
.badge-band b{display:block;font-size:6.8px;font-weight:700;text-transform:uppercase;line-height:10px}
.badge-band i{display:block;font-size:6.5px}
.service-lead{left:214px;width:450px;font-size:9px;line-height:17px;color:var(--ink)}
.service-body{left:214px;width:500px;font-size:6.4px;line-height:16.5px;color:var(--muted)}
.divider{left:63px;width:649px;height:1px;background:var(--line)}

/* sectors band */
.sectors{left:0;top:934px;width:775px;height:84px;background:var(--band)}
.sector{position:absolute;top:34px;transform:translateX(-50%);font-size:10px;color:var(--soft);font-weight:500;font-family:"Roboto",sans-serif;white-space:nowrap;text-transform:uppercase;letter-spacing:.5px}

/* footer */
.footer{left:0;top:1018px;width:775px;height:182px;background:var(--footer);color:#fff}
.footer .brand-name{color:#fff;font-size:12px}
.footer .brand-mark{background:#fff;width:11px;height:11px}
.f-text{font-size:7px;line-height:15px}
.f-head{font-family:"Roboto",sans-serif;font-size:10px;font-weight:500;letter-spacing:.2px}
.f-link{font-size:7px}
.news-input{left:380px;top:93px;width:108px;height:25px;background:#18608c;color:#b9cfdd;font-size:6.8px;padding-left:8px;line-height:25px}
.news-btn{left:488px;top:93px;width:52px;height:25px;background:#fff;color:var(--navy);font-size:10px;display:flex;align-items:center;justify-content:center}
.social{width:17px;height:17px;border-radius:50%;background:#fff}
</style>
</head>
<body>

<header>
  <div class="abs" style="left:63px;top:24px">
    <div class="brand"><span class="brand-mark"></span><span class="brand-name">BRISK HARBOR</span></div>
    <div class="brand-tag">CLAIMS RECOVERY SERVICES</div>
  </div>
  <div class="abs call">
    <span class="call-icon"><svg width="10" height="10" viewBox="0 0 24 24"><path d="M6.6 10.8a15 15 0 0 0 6.6 6.6l2.2-2.2a1 1 0 0 1 1-.25 11.4 11.4 0 0 0 3.6.57 1 1 0 0 1 1 1V20a1 1 0 0 1-1 1A17 17 0 0 1 3 4a1 1 0 0 1 1-1h3.5a1 1 0 0 1 1 1c0 1.25.2 2.45.57 3.6a1 1 0 0 1-.25 1z" fill="#0f5a85"/></svg></span>
    <span>Call Us Today : <strong>(+100) 555-0142</strong></span>
  </div>
  <div class="abs quote-btn">REQUEST A QUOTE</div>
</header>

<nav class="abs main-nav">
  <div class="abs nav-active"></div>
  <span class="nav-item" style="left:107px">Home</span>
  <span class="nav-item" style="left:197px">About Us</span>
  <span class="nav-item" style="left:292px">Debt Management</span>
  <span class="nav-item" style="left:387px">Services</span>
  <span class="nav-item" style="left:481px">Sectors</span>
  <span class="nav-item" style="left:581px">Restructuring</span>
  <span class="nav-item" style="left:689px">Contact Us</span>
</nav>

<section class="abs hero" role="img" aria-label="Businessman's hand stopping a row of falling wooden dominoes on a dark desk"></section>
<svg class="abs" style="left:36px;top:212px" width="12" height="34" viewBox="0 0 12 34"><path d="M11 1 1 17l10 16" fill="none" stroke="#8a96a3" stroke-width="1"/></svg>
<svg class="abs" style="left:727px;top:212px" width="12" height="34" viewBox="0 0 12 34"><path d="M1 1l10 16L1 33" fill="none" stroke="#8a96a3" stroke-width="1"/></svg>
<div class="abs hero-title">MANAGING YOUR MONEY</div>
<div class="abs hero-sub">RECOVERING YOUR RELATIONSHIPS</div>

<main>
  <h1 class="abs section-title">OUR SERVICES</h1>
  <p class="abs section-intro">Intelligent lending opens doors and allows ambitious individuals and fledgling businesses to grow. But without careful planning and management, debt can become overwhelming.</p>

  <article>
    <div class="abs service-badge" style="left:64px;top:465px">
      <svg width="40" height="40" viewBox="0 0 40 40"><rect x="6" y="24" width="6" height="10" fill="#0f5a85"/><rect x="17" y="16" width="6" height="18" fill="#0f5a85"/><rect x="28" y="8" width="6" height="26" fill="#0f5a85"/></svg>
      <div class="badge-band"><b>Debt Management</b><i>Planning</i></div>
    </div>
    <p class="abs service-lead" style="top:465px">Structured debt management plans for government entities, healthcare providers, banks and commercial businesses of every size.</p>
    <p class="abs service-body" style="top:503px">We review your receivables, classify outstanding accounts by risk and age, and build a clear recovery plan with agreed timelines. Our team works alongside your finance department to keep records accurate and cash flow predictable. Regular reports show progress on every account, so you always know where each balance stands and what action comes next. Early attention to overdue accounts keeps small balances from becoming long-term losses.</p>
  </article>
  <div class="abs divider" style="top:604px"></div>

  <article>
    <div class="abs service-badge" style="left:64px;top:621px">
      <svg width="40" height="40" viewBox="0 0 40 40"><circle cx="20" cy="20" r="14" fill="none" stroke="#0f5a85" stroke-width="3"/><path d="M13 20l5 5 9-10" fill="none" stroke="#0f5a85" stroke-width="3"/></svg>
      <div class="badge-band"><b>Debt Collection</b><i>Recovery</i></div>
    </div>
    <p class="abs service-lead" style="top:620px">Professional, respectful debt collection that recovers what you are owed while protecting the relationships behind every account.</p>
    <p class="abs service-body" style="top:658px">Our collectors follow a firm but courteous process, from first reminder through negotiated payment arrangements. Every contact is documented and handled in line with local regulations across the UAE. We tailor the approach to each debtor, whether an individual, a small business or a large organisation, to reach settlement quickly and keep your reputation intact. Where needed, we coordinate legal follow-up with trusted partners.</p>
  </article>
  <div class="abs divider" style="top:760px"></div>

  <article>
    <div class="abs service-badge" style="left:64px;top:776px">
      <svg width="40" height="40" viewBox="0 0 40 40"><path d="M8 14h20l-5-5M32 26H12l5 5" fill="none" stroke="#0f5a85" stroke-width="3"/></svg>
      <div class="badge-band"><b>Loan Settlement</b><i>Restructuring</i></div>
    </div>
    <p class="abs service-lead" style="top:775px">Loan settlement and restructuring that turns difficult obligations into manageable, realistic repayment schedules.</p>
    <p class="abs service-body" style="top:813px">We negotiate with lenders and borrowers to find terms both sides can accept, whether that means revised instalments, extended tenors or a one-time settlement. For banks and finance companies we reduce non-performing balances; for SMEs we create breathing room to keep operating. Each agreement is drafted clearly and tracked to completion, giving all parties confidence in the outcome.</p>
  </article>
</main>

<section class="abs sectors" aria-label="Sectors we serve">
  <span class="sector" style="left:110px">Government</span>
  <span class="sector" style="left:230px">Healthcare</span>
  <span class="sector" style="left:345px">Banks</span>
  <span class="sector" style="left:450px">Finance</span>
  <span class="sector" style="left:550px">SMEs</span>
  <span class="sector" style="left:660px">Commercial</span>
</section>

<footer class="abs footer">
  <div class="abs" style="left:63px;top:30px">
    <div class="brand"><span class="brand-mark"></span><span class="brand-name">BRISK HARBOR</span></div>
  </div>
  <p class="abs f-text" style="left:63px;top:65px;width:135px">Sed ut perspiciatis unde omnis isteers accusantium doloremque laudantium, totam rem aperiam, eaque ipsa quae ab illo inventore veritatis et...</p>

  <h3 class="abs f-head" style="left:241px;top:24px">NAVIGATION</h3>
  <span class="abs f-link" style="left:241px;top:46px">Home</span>
  <span class="abs f-link" style="left:241px;top:63px">About Us</span>
  <span class="abs f-link" style="left:241px;top:80px">Services</span>
  <span class="abs f-link" style="left:241px;top:97px">Sectors</span>
  <span class="abs f-link" style="left:285px;top:46px">Collection</span>
  <span class="abs f-link" style="left:285px;top:63px">Settlement</span>
  <span class="abs f-link" style="left:285px;top:80px">Contact Us</span>

  <h3 class="abs f-head" style="left:380px;top:24px">NEWSLETTER</h3>
  <p class="abs f-text" style="left:380px;top:43px;width:170px;font-size:6.8px;line-height:13.5px">Excepteur sint occaecat cupidatat non proident, sunt in culpa qui officia deserunt mollit anim enim ipsam voluptatem quia...</p>
  <div class="abs news-input">Enter your email address</div>
  <div class="abs news-btn">Sign Up</div>

  <h3 class="abs f-head" style="left:590px;top:25px">CONTACT US</h3>
  <p class="abs f-text" style="left:591px;top:47px;font-size:7px;line-height:14.5px">2210 Harbor Lane;<br>Creek Road, Unit-1180</p>
  <svg class="abs" style="left:592px;top:88px" width="12" height="12" viewBox="0 0 24 24"><path d="M6.6 10.8a15 15 0 0 0 6.6 6.6l2.2-2.2a1 1 0 0 1 1-.25 11.4 11.4 0 0 0 3.6.57 1 1 0 0 1 1 1V20a1 1 0 0 1-1 1A17 17 0 0 1 3 4a1 1 0 0 1 1-1h3.5a1 1 0 0 1 1 1c0 1.25.2 2.45.57 3.6a1 1 0 0 1-.25 1z" fill="none" stroke="#fff" stroke-width="1.5"/></svg>
  <span class="abs" style="left:614px;top:86px;font-size:11px">(900) 555-0187</span>
  <svg class="abs" style="left:592px;top:111px" width="13" height="10" viewBox="0 0 13 10"><rect x=".5" y=".5" width="12" height="9" fill="none" stroke="#fff"/><path d="M.5 .5l6 5 6-5" fill="none" stroke="#fff"/></svg>
  <span class="abs" style="left:614px;top:110px;font-size:7.5px">hello@briskharbor.example</span>

  <span class="abs" style="left:63px;top:159px;font-size:7px">Copyrights©briskharbor.2016 | Allrights Reserved.</span>
  <span class="abs" style="left:583px;top:159px;font-size:7px">Connect With Us:</span>
  <span class="abs social" style="left:650px;top:155px" role="img" aria-label="Social link"></span>
  <span class="abs social" style="left:672px;top:155px" role="img" aria-label="Social link"></span>
  <span class="abs social" style="left:694px;top:155px" role="img" aria-label="Social link"></span>
</footer>

</body>
</html>
```